Designing a brochures for an educational counseling service provider

We would like a 4 sided design on a 11x8.5 paper, half folded. I have including a sample design we did to give you an idea of what we envision but we welcome creativity to make beautiful looking flyers. Text for the flier is included as well as our logo.
- The most important thing is capturing our audience/market. We will be handing these flies to schools, organizations and individual clients.

www.pvrlearningadvisors.example

Target Market(s)

We are targeting international students wanting to study in the U.S and Canada.

Industry/Entity Type

Education

Requirements
Must have
• - Clean and clear
• - Our logo should visible and well placed.
• - Could you the pictures of students, libraries and school buildings or you could use the pictures we already have.
Nice to have
• We would like this to match business cards.

```html
<!DOCTYPE html>
<html lang="en">
<head>
<meta charset="utf-8">
<title>PVR Learning Advisors – Brochure</title>
<link href="https://fonts.googleapis.com/css2?family=Arimo:wght@400;700&display=swap" rel="stylesheet">
<style>
  :root{
    --backdrop:#8e8e8e;
    --paper:#ffffff;
    --orange:#f7941d;
    --orange-deep:#e8731a;
    --navy:#262b86;
    --navy-deep:#1b1f66;
    --heading:#2e4aa0;
    --ink:#333338;
    --photo-warm-a:#e9b48a;
    --photo-warm-b:#c7623f;
    --photo-green-a:#7fa65a;
    --photo-green-b:#3f6a33;
    --photo-lib-a:#a88c6c;
    --photo-lib-b:#6b4f3a;
  }
  *{box-sizing:border-box;margin:0;padding:0}
  html,body{width:1200px;height:582px;overflow:hidden}
  body{background:var(--backdrop);font-family:"Arimo",Arial,sans-serif;color:var(--ink);position:relative}
  .page{position:absolute;top:78px;width:272px;height:428px;background:var(--paper);overflow:hidden;box-shadow:0 4px 10px rgba(0,0,0,.35)}
  .page-front{left:30px}
  .spread{position:absolute;left:330px;top:78px;width:548px;height:428px;box-shadow:0 4px 10px rgba(0,0,0,.35)}
  .spread .page{top:0;box-shadow:none}
  .page-inside-left{left:0}
  .page-inside-right{left:276px}
  .page-back{left:900px}
  .art{position:absolute;inset:0;width:100%;height:100%}
  .layer{position:absolute}

  /* brand */
  .brand{left:0;right:0;top:30px;display:flex;align-items:center;justify-content:center;gap:7px}
  .brand-dot{width:22px;height:22px;border-radius:50%;background:var(--orange)}
  .brand-name{font-weight:700;font-size:12px;color:var(--navy);letter-spacing:.4px;line-height:1.15}
  .brand-tag{position:absolute;left:0;right:0;top:60px;text-align:center;font-size:5px;letter-spacing:1.3px;color:var(--navy)}

  .cover-tagline{left:14px;right:14px;top:338px;text-align:center;font-size:8.6px;line-height:1.3;color:#222}
  .service-icons{left:14px;right:14px;top:368px;display:flex;justify-content:space-around}
  .service{display:flex;flex-direction:column;align-items:center;gap:4px;width:56px}
  .service svg{width:25px;height:25px}
  .service span{font-size:5px;color:#333;white-space:nowrap}

  /* inside text */
  h2.section-title{font-size:8.5px;font-weight:700;color:var(--heading);margin:7px 0 2px;letter-spacing:.2px}
  .copy p,.copy li{font-size:5.45px;line-height:1.38;color:#3a3a40}
  .copy p+p{margin-top:4px}
  .about{left:16px;top:92px;width:244px}
  .about .narrow{width:135px}
  .services{left:10px;top:6px;width:254px}
  .services .intro{width:160px}
  .package-label{font-style:italic;font-weight:700;color:var(--heading);font-size:6px !important}
  .checklist{list-style:none;margin:2px 0 0 6px}
  .checklist li{position:relative;padding-left:8px}
  .checklist li::before{content:"";position:absolute;left:0;top:1.6px;width:4px;height:4px;border-radius:50%;background:#666}
  .membership{font-weight:700;font-style:italic;color:#222}

  /* back */
  .contact{left:0;right:0;top:307px;text-align:center}
  .contact h2{font-size:9px;font-weight:400;color:#222;letter-spacing:.3px;margin-bottom:4px}
  .contact p{font-size:5.6px;line-height:1.35;color:#333}
  .contact-bar{position:absolute;left:28px;right:28px;top:382px;height:19px;background:linear-gradient(var(--navy),var(--navy-deep));color:#fff;text-align:center;font-size:5.4px;line-height:1.3;padding-top:2.5px}
</style>
</head>
<body>

<!-- Front cover -->
<section class="page page-front" aria-label="Front cover">
  <svg class="art" viewBox="0 0 272 428">
    <defs>
      <linearGradient id="groupTone" x1="0" y1="0" x2="1" y2="1">
        <stop offset="0" stop-color="var(--photo-warm-a)"/>
        <stop offset="1" stop-color="var(--photo-warm-b)"/>
      </linearGradient>
    </defs>
    <path d="M0 0 H60 Q20 60 0 130 Z" fill="var(--orange)"/>
    <path d="M0 0 H40 Q8 50 0 100 Z" fill="var(--orange-deep)"/>
    <path d="M0 150 Q140 120 272 140 V310 Q150 285 0 330 Z" fill="url(#groupTone)" role="img" aria-label="Photo: a group of smiling international students standing together"/>
    <path d="M110 175 Q200 150 272 140 V200 Q200 215 110 175 Z" fill="var(--navy)"/>
    <path d="M120 180 Q200 200 272 205 V215 Q200 215 120 180 Z" fill="var(--orange)"/>
    <path d="M0 300 Q130 300 272 270 V285 Q140 320 0 330 Z" fill="var(--navy)"/>
    <path d="M0 322 Q140 318 272 280 V300 Q140 335 0 335 Z" fill="var(--orange)"/>
    <path d="M272 0 V90 Q240 40 180 0 Z" fill="#f4f4f6"/>
  </svg>
  <div class="layer brand"><span class="brand-dot"></span><span class="brand-name">PVR LEARNING<br>ADVISORS</span></div>
  <div class="brand-tag">INTERNATIONAL STUDENTS SOLUTIONS</div>
  <p class="layer cover-tagline">A full-services international educational consulting international group serving students and families across the globe.</p>
  <div class="layer service-icons">
    <div class="service">
      <svg viewBox="0 0 26 26"><circle cx="13" cy="13" r="13" fill="var(--orange)"/><path d="M7 10 L13 6 L19 10 Z M8 11h10v1H8z M9 12.5h1.6v6H9z M12.2 12.5h1.6v6h-1.6z M15.4 12.5H17v6h-1.6z M7.5 19h11v1.3h-11z" fill="#fff"/></svg>
      <span>Boarding Schools</span>
    </div>
    <div class="service">
      <svg viewBox="0 0 26 26"><circle cx="13" cy="13" r="13" fill="var(--orange)"/><rect x="7.5" y="8" width="9" height="11" fill="none" stroke="#fff" stroke-width="1.3"/><path d="M12 16 L19 8.5 L20.2 9.7 L13.2 17.2 L11.6 17.6 Z" fill="#fff"/></svg>
      <span>College Admission</span>
    </div>
    <div class="service">
      <svg viewBox="0 0 26 26"><circle cx="13" cy="13" r="13" fill="var(--orange)"/><path d="M8 11 A6 6 0 0 1 18 9" fill="none" stroke="#fff" stroke-width="1.6"/><path d="M18 6 V10 H14" fill="none" stroke="#fff" stroke-width="1.6"/><path d="M18 15 A6 6 0 0 1 8 17" fill="none" stroke="#fff" stroke-width="1.6"/><path d="M8 20 V16 H12" fill="none" stroke="#fff" stroke-width="1.6"/></svg>
      <span>Transfer Students</span>
    </div>
    <div class="service">
      <svg viewBox="0 0 26 26"><circle cx="13" cy="13" r="13" fill="var(--orange)"/><path d="M5 11 L13 7.5 L21 11 L13 14.5 Z" fill="#fff"/><path d="M9 13 V17 Q13 19.5 17 17 V13 L13 15 Z" fill="#fff"/><path d="M20 11.3 V16" stroke="#fff" stroke-width="1"/></svg>
      <span>Graduate Students</span>
    </div>
  </div>
</section>

<!-- Inside spread -->
<div class="spread">
  <section class="page page-inside-left" aria-label="Inside left page">
    <svg class="art" viewBox="0 0 272 428">
      <defs>
        <linearGradient id="campusTone" x1="0" y1="0" x2="0" y2="1">
          <stop offset="0" stop-color="var(--photo-green-a)"/>
          <stop offset="1" stop-color="var(--photo-green-b)"/>
        </linearGradient>
        <linearGradient id="libraryTone" x1="0" y1="0" x2="1" y2="1">
          <stop offset="0" stop-color="var(--photo-lib-a)"/>
          <stop offset="1" stop-color="var(--photo-lib-b)"/>
        </linearGradient>
      </defs>
      <path d="M0 8 Q120 4 272 0 V10 Q120 10 0 22 Z" fill="var(--orange)"/>
      <path d="M0 22 Q110 12 200 12 Q110 24 0 40 Z" fill="var(--navy)"/>
      <path d="M272 18 Q230 40 200 80 L272 90 Z" fill="var(--navy)"/>
      <circle cx="208" cy="66" r="52" fill="#d0d0d0"/>
      <circle cx="208" cy="66" r="48" fill="url(#campusTone)" role="img" aria-label="Photo: students sitting on a campus lawn in front of school buildings"/>
      <path d="M0 230 Q150 240 272 200 V378 Q140 372 0 392 Z" fill="url(#libraryTone)" role="img" aria-label="Photo: students studying together at tables in a school library"/>
      <path d="M0 390 Q140 370 272 376 V390 Q140 388 0 404 Z" fill="var(--navy)"/>
      <path d="M0 402 Q140 392 272 398 V428 H0 Z" fill="var(--orange)"/>
    </svg>
    <div class="layer about copy">
      <h2 class="section-title">ABOUT US:</h2>
      <p class="narrow">Our mission is to make quality education accessible and affordable to the families we serve. Our services are designed with the child's future in mind. Whether one is seeking an academic or non-academic environment, it is important to us that we set our clients up for success.</p>
      <p>We are a family-centered organization and our goals are the same as those of our clients; for their child to thrive and reach their goals and dreams. With over 10 years of experience in the business, we are aware of the financial obstacles created by the ever increasing cost in education. Our expert consultants work closely with families to map out their educational budget and find the best affordable and quality educational options.</p>
    </div>
  </section>

  <section class="page page-inside-right" aria-label="Inside right page">
    <svg class="art" viewBox="0 0 272 428">
      <path d="M120 0 Q210 16 272 52 V0 Z" fill="var(--orange)"/>
      <path d="M190 0 Q240 12 272 30 V0 Z" fill="var(--navy)"/>
      <path d="M0 400 Q140 380 272 392 V404 Q140 396 0 414 Z" fill="var(--navy)"/>
      <path d="M0 412 Q140 402 272 408 V428 H0 Z" fill="var(--orange)"/>
    </svg>
    <div class="layer services copy">
      <h2 class="section-title">SERVICES:</h2>
      <p class="intro">Finding the right school or program for your child is one of the most important decisions your family will make. The right choice will make a major impact on your child's future.</p>
      <p class="package-label">Our package includes:</p>
      <ul class="checklist">
        <li>Intake interview.</li>
        <li>Present range of options based on needs and goals of the family.</li>
        <li>Interview coaching.</li>
        <li>Assistance with application and essays.</li>
        <li>Updates on student progress throughout their enrollment with the school.</li>
        <li>Advisement on financial documents and visa applications.</li>
      </ul>
      <h2 class="section-title">BOARDING SCHOOLS:</h2>
      <p>Students who want the best out of their grade school experience are likely to choose boarding schools because they are proven to better prepare students for university. North American boarding schools provide a quality dynamic experience that will facilitate personal growth in independence, leadership, and confidence as well as provide the academic curriculum necessary to prepare students for university.</p>
      <h2 class="section-title">COLLEGE ADMISSION:</h2>
      <p>As Educational Consultants, we specialize in college/university admissions and we understand how confusing, time-consuming, and stressful the application process can be. Our experienced counselors are here to answer your questions and guide you step by step. As Parents and students may have limited access to information on schools, may not know or understand the entire process as a whole, nor where/how to begin, our experts counselors have a solutions.</p>
      <p>Clients increase the odds of admissions with our comprehensive plan of action. We believe that regardless of a student's level of involvement in extra-curricular activities or preparedness, they still possess something they can offer to the university; therefore we help them shine on their college applications.</p>
      <h2 class="section-title">TRANSFER STUDENTS:</h2>
      <p>Need to find a school an alternative school that is a better match for you? We work with students and families to transfer from one school to another.</p>
      <h2 class="section-title">SCHOLARSHIPS:</h2>
      <p>Funding the education for your children in some of the world's top schools can be very expensive as tuition and fees increase at an average of 4% every year. We work with you to determine the budget for your family, applying to scholarship available and guide you through the financial aid process.</p>
      <p>Over <b>70%</b> of our clients have been awarded scholarships or Financial Aid, making your education goals attainable an affordable and your children education possible.</p>
      <p>Include at the bottom of last page <span class="membership">"Our consultants are members of ALA, the leading association for educational consultants in North America."</span></p>
    </div>
  </section>
</div>

<!-- Back cover -->
<section class="page page-back" aria-label="Back cover">
  <svg class="art" viewBox="0 0 272 428">
    <defs>
      <linearGradient id="studentsTone" x1="1" y1="0" x2="0" y2="1">
        <stop offset="0" stop-color="var(--photo-warm-a)"/>
        <stop offset="1" stop-color="#d58a5e"/>
      </linearGradient>
    </defs>
    <path d="M140 0 Q230 20 272 90 V0 Z" fill="var(--orange)"/>
    <path d="M200 0 Q250 20 272 50 V0 Z" fill="var(--orange-deep)"/>
    <path d="M0 90 Q60 150 150 110 Q220 80 272 80 V270 Q150 250 0 290 Z" fill="url(#studentsTone)" role="img" aria-label="Photo: a group of happy students giving a thumbs up"/>
    <path d="M0 90 Q40 140 130 120 Q40 160 0 150 Z" fill="var(--navy)"/>
    <path d="M0 270 Q140 240 272 238 V256 Q140 262 0 290 Z" fill="var(--navy)"/>
    <path d="M0 286 Q140 258 272 252 V262 Q140 272 0 296 Z" fill="var(--orange)"/>
  </svg>
  <div class="layer contact">
    <h2>CONTACT US</h2>
    <p>Executive Director &amp; Independent<br>Educational Consultant<br>PVR Learning Advisors, LLC<br>418 Meadow Lane<br>Suite 12B, Fairbrook, TX 75001</p>
  </div>
  <div class="contact-bar">Phone: 555-014-0199<br>Email: info@pvrlearningadvisors.example</div>
</section>

</body>
</html>
```